Redesign of business card for Cedar Ridge Mechanical

We are looking for a new design for our business cards for Cedar Ridge Mechanical. We are a plumbing & HVAC construction company, operating on the West Coast of Canada and USA. Logo attached.
Industry/Entity Type
Construction - Plumbing & HVAC
Contact Information for Business Card
Name, address, phone numbers, email, website address
Look and feel
Each slider illustrates characteristics of the customer's brand and the style your logo design should communicate.

```html
<!DOCTYPE html>
<html lang="en">
<head>
<meta charset="utf-8">
<title>Cedar Ridge Mechanical – Business Card</title>
<link href="https://fonts.googleapis.com/css2?family=Montserrat:wght@400;700;800&display=swap" rel="stylesheet">
<style>
  :root{
    --ink:#111111;
    --paper:#ffffff;
    --muted:#555555;
    --stage:#e6e6e6;
  }
  *{box-sizing:border-box;margin:0;padding:0}
  html,body{width:1200px;height:913px;overflow:hidden}
  body{background:var(--stage);font-family:"Montserrat",sans-serif;color:var(--ink);position:relative}
  .card{position:absolute;left:280px;width:640px;height:366px;background:var(--paper);border-radius:22px;box-shadow:0 6px 18px rgba(0,0,0,.18);overflow:hidden}
  .card--front{top:60px}
  .card--back{top:487px}

  .brand{position:absolute;display:flex;align-items:center;gap:14px;font-weight:800;text-transform:uppercase;color:var(--ink);white-space:nowrap}
  .brand__square{display:block;background:var(--ink)}
  .card--front .brand{left:50%;top:50%;transform:translate(-50%,-50%);font-size:34px;letter-spacing:1px}
  .card--front .brand__square{width:44px;height:44px}
  .card--back .brand{left:50%;top:78px;transform:translateX(-50%);font-size:24px;letter-spacing:1px}
  .card--back .brand__square{width:32px;height:32px}

  .person{position:absolute;left:60px;top:200px;text-align:right;width:230px}
  .person__name{font-size:24px;font-weight:800;letter-spacing:1px}
  .person__title{font-size:16px;color:var(--muted);margin-top:2px}

  .divider{position:absolute;left:318px;top:165px;width:1.5px;height:100px;background:var(--ink)}

  .contacts{position:absolute;left:342px;top:160px;list-style:none}
  .contacts li{display:flex;align-items:center;gap:10px;font-size:15px;line-height:28px}
  .contacts svg{width:15px;height:15px;flex:none}

  .band{position:absolute;right:0;top:296px;width:360px;height:28px;background:var(--ink);color:var(--paper);font-size:14px;display:flex;align-items:center;padding-left:18px;letter-spacing:.3px}
  .band__mark{position:absolute;right:14px;top:6px;width:16px;height:16px;border:2px solid var(--paper)}
  .rule{position:absolute;left:0;right:0;top:330px;height:8px;background:var(--ink)}
</style>
</head>
<body>
  <section class="card card--front" aria-label="Card front">
    <div class="brand"><span class="brand__square"></span>Cedar Ridge Mechanical</div>
  </section>

  <section class="card card--back" aria-label="Card back">
    <div class="brand"><span class="brand__square"></span>Cedar Ridge Mechanical</div>

    <div class="person">
      <p class="person__name">DANIEL HART</p>
      <p class="person__title">Managing Director</p>
    </div>

    <div class="divider"></div>

    <ul class="contacts">
      <li><svg viewBox="0 0 16 16"><path d="M4 1h3l1 4-2 1.5a9 9 0 0 0 3.5 3.5L11 8l4 1v3c0 1-1 2-2 2A12 12 0 0 1 2 3c0-1 1-2 2-2z" fill="#111"/></svg>123 456 789</li>
      <li><svg viewBox="0 0 16 16"><rect x="1" y="3" width="14" height="10" rx="1.5" fill="#111"/><path d="M1.5 4 8 9l6.5-5" stroke="#fff" stroke-width="1.3" fill="none"/></svg>info@yourmail.com</li>
      <li><svg viewBox="0 0 16 16"><circle cx="8" cy="8" r="7" fill="#111"/><path d="M1 8h14M8 1c-3 3-3 11 0 14M8 1c3 3 3 11 0 14" stroke="#fff" stroke-width="1" fill="none"/></svg>www.yourwebsite.com</li>
    </ul>

    <div class="band">Your address, City State, Zip 1234<span class="band__mark"></span></div>
    <div class="rule"></div>
  </section>
</body>
</html>
```